update of B2B website and conversion to single page

The current website needs to be modernized. I want what is commonly called a single page website. It is not actually a single page. See some examples here:
https://www.plivenor.example/
https://www.quorbel.example/
https://www.trindavex.example/
Most or all graphics will be replaced.
Please see the attached spreadsheet for a rough draft of the home page layout. Convert the existing website at https://www.zolvarin.example/ to a single page website. We will provide the page content. You will provide all of the design, graphics, development, production deployment. etc. The look and feel should be corporate, polished, premium.

```html
<!DOCTYPE html>
<html lang="en">
<head>
<meta charset="utf-8">
<title>Zolvarin Data</title>
<link href="https://fonts.googleapis.com/css2?family=Roboto:wght@400;500;700&family=Open+Sans:ital,wght@0,400;0,600;0,700;1,400&display=swap" rel="stylesheet">
<style>
:root{
  --orange:#f7b500;
  --navy:#1f2b72;
  --navy-deep:#18215a;
  --ink:#1e1e1e;
  --body:#444;
  --line:#c9cde0;
  --pale:#f3f4fb;
  --black:#0c0c0c;
}
*{box-sizing:border-box;margin:0;padding:0}
html,body{width:1200px;height:4348px;overflow:hidden}
body{position:relative;background:#fff;font-family:'Open Sans',sans-serif;color:var(--body)}
.abs{position:absolute}
h2.section-title{position:absolute;left:0;width:1200px;text-align:center;font-family:'Roboto',sans-serif;font-weight:500;font-size:47px;color:var(--ink);letter-spacing:1px}
svg{display:block}

/* header */
.site-header{position:absolute;top:0;left:0;width:1200px;height:85px;background:#fff}
.brand{position:absolute;left:100px;top:22px;display:flex;align-items:center;gap:12px}
.brand-dot{width:38px;height:38px;border-radius:50%;background:var(--navy)}
.brand-name{font-family:'Roboto',sans-serif;font-weight:700;font-size:30px;color:var(--navy)}
.nav{position:absolute;right:92px;top:34px;display:flex;gap:28px;font-family:'Roboto',sans-serif;font-weight:500;font-size:15px;color:#222}
.nav .active{color:var(--orange)}

/* hero */
.hero{position:absolute;top:85px;left:0;width:1200px;height:547px;background:linear-gradient(180deg,#8fb2d9 0%,#b7c7d6 30%,#6f8b74 52%,#4d7a34 70%,#5f8f2f 100%)}
.hero h1{position:absolute;top:150px;width:100%;text-align:center;font-family:'Roboto',sans-serif;font-weight:700;font-size:82px;color:#fff;letter-spacing:2px}
.hero p{position:absolute;top:270px;width:100%;text-align:center;font-size:22px;font-weight:600;color:#fff}
.dots{position:absolute;top:470px;left:570px;display:flex;gap:6px}
.dots span{width:11px;height:11px;border-radius:50%;border:2px solid #fff}
.dots span:first-child{background:#fff}

/* easy */
.easy-title{left:110px;top:778px;font-family:'Roboto',sans-serif;font-weight:700;font-size:44px;color:var(--ink)}
.easy-text{left:112px;top:858px;width:430px;font-size:13px;line-height:24px;color:#555}
.easy-divider{left:627px;top:775px;width:1px;height:110px;background:#bbb}
.feature{position:absolute;left:706px;display:flex;align-items:center;gap:28px}
.feature .ring{width:88px;height:88px;border-radius:50%;border:2px solid var(--navy);display:flex;align-items:center;justify-content:center}
.feature p{font-size:22px;line-height:28px;color:#222;font-weight:600}

/* services */
.services{position:absolute;top:1140px;left:0;width:1200px;height:772px;background:linear-gradient(135deg,var(--navy-deep),#2b3b8f 50%,var(--navy-deep))}
.services h2.section-title{color:#fff;top:65px}
.svc-card{position:absolute;top:175px;width:463px;height:518px;background:#fff}
.svc-photo{height:263px}
.svc-badge{position:absolute;left:191px;top:223px;width:80px;height:80px;border-radius:50%;background:var(--orange);border:5px solid #fff;display:flex;align-items:center;justify-content:center}
.svc-card h3{position:absolute;top:345px;width:100%;text-align:center;font-family:'Roboto',sans-serif;font-weight:700;font-size:26px;color:var(--ink)}
.svc-list{position:absolute;top:392px;width:100%;list-style:none;text-align:center;font-size:15px;line-height:30px;color:#333}

.tick{display:inline-block;width:13px;height:11px;margin-right:8px;vertical-align:0}

/* connectors / support cards */
.box{position:absolute;background:#fff;border:2px solid var(--line)}
.box .icon{position:absolute;left:42px;top:22px}
.box h3{position:absolute;left:42px;font-family:'Roboto',sans-serif;font-weight:500;font-size:24px;color:var(--ink)}
.box ul{position:absolute;left:42px;list-style:none;font-size:15px;line-height:27px;color:#333}
.box .soon{position:absolute;left:42px;font-size:15px;line-height:27px;font-style:italic;color:#333}

.support{position:absolute;top:2535px;left:0;width:1200px;height:500px;background:var(--pale)}

/* blog */
.post{position:absolute;top:3218px;width:313px}
.post-photo{height:202px}
.post h3{margin-top:30px;font-family:'Roboto',sans-serif;font-weight:500;font-size:22px;color:var(--ink)}
.meta{margin-top:10px;font-size:14px;color:#333;display:flex;gap:10px;align-items:center}
.post p{margin-top:18px;font-size:14px;line-height:24px;color:#555}
.read-more{display:block;margin-top:24px;font-size:13px;font-weight:700;color:var(--orange)}

/* contact */
.contact{position:absolute;top:3730px;left:0;width:1200px;height:618px;background:var(--black);color:#fff}
.contact h2.section-title{color:#fff;top:72px}
.contact h4{position:absolute;top:180px;font-family:'Roboto',sans-serif;font-weight:700;font-size:20px;color:#fff}
.field{position:absolute;height:33px;background:#fff;border:none;font-size:12px;color:#888;padding:9px 10px}
.submit{position:absolute;left:640px;top:445px;width:100px;height:34px;border-radius:17px;background:var(--orange);color:#fff;font-family:'Roboto',sans-serif;font-weight:700;font-size:14px;text-align:center;line-height:34px}
.info{position:absolute;left:795px;display:flex;align-items:center;gap:22px;font-size:14px;line-height:22px;color:#eee}
.info .pin{width:34px;height:34px;border-radius:50%;background:#2a2a2a;border:1px solid var(--orange);display:flex;align-items:center;justify-content:center}
.socials{position:absolute;left:795px;top:440px;display:flex;gap:10px}
.socials span{width:32px;height:32px;border-radius:50%;background:#2f67c8}
.socials span:last-child{background:#c8323a}
.footline{position:absolute;left:0;top:535px;width:1200px;height:1px;background:#2a2a2a}
.copyright{position:absolute;top:562px;width:100%;text-align:center;font-size:13px;color:#ccc}
</style>
</head>
<body>

<svg width="0" height="0" style="position:absolute">
  <defs>
    <symbol id="tick" viewBox="0 0 13 11"><path d="M1 6l4 4 7-9" fill="none" stroke="#1f2b72" stroke-width="2.6"/></symbol>
  </defs>
</svg>

<header class="site-header">
  <div class="brand"><span class="brand-dot"></span><span class="brand-name">Zolvarin Data</span></div>
  <nav class="nav">
    <span class="active">HOME</span><span>ABOUT</span><span>SERVICES</span><span>CONNECTORS</span><span>SUPPORT</span><span>BLOG</span><span>CONTACT</span>
    <svg width="15" height="15" viewBox="0 0 15 15"><circle cx="6" cy="6" r="4.5" fill="none" stroke="#222" stroke-width="2"/><path d="M9.5 9.5l4 4" stroke="#222" stroke-width="2.4"/></svg>
  </nav>
</header>

<section class="hero" role="img" aria-label="City park lawn with people relaxing and skyline behind">
  <h1>ZOLVARIN DATA</h1>
  <p>Enterprise Data Quality and Master Data Management Made Easy</p>
  <div class="dots"><span></span><span></span><span></span><span></span></div>
</section>

<section class="easy">
  <h2 class="abs easy-title">EASY</h2>
  <p class="abs easy-text">Zolvarin Data was founded in 1998 as a consulting company focused on the implementation of enterprise applications. Our team was comprised of senior software developers who had worked for many of the leading commercial application vendors.</p>
  <div class="abs easy-divider"></div>
  <div class="feature" style="top:731px">
    <div class="ring"><svg width="34" height="38" viewBox="0 0 34 38"><rect x="5" y="9" width="24" height="27" rx="2" fill="#f7b500"/><rect x="2" y="5" width="30" height="4" fill="#f7b500"/><rect x="12" y="1" width="10" height="4" fill="#f7b500"/><path d="M12 14v17M17 14v17M22 14v17" stroke="#fff" stroke-width="2"/></svg></div>
    <p>Cleanse addresses<br>in 5 minutes</p>
  </div>
  <div class="feature" style="top:833px">
    <div class="ring"><svg width="36" height="36" viewBox="0 0 36 36"><path d="M3 3l11 11M14 6v8H6M33 33L22 22M22 30v-8h8" fill="none" stroke="#f7b500" stroke-width="4"/></svg></div>
    <p>Match and Merge records<br>in 10 minutes</p>
  </div>
  <div class="feature" style="top:936px">
    <div class="ring"><svg width="38" height="32" viewBox="0 0 38 32"><path d="M2 4h12l4 4h16v6H8L2 28z" fill="#f7b500"/><path d="M9 14h28l-7 16H2z" fill="#f7b500" opacity=".8"/></svg></div>
    <p>Master records in<br>60 minutes</p>
  </div>
</section>

<section class="services">
  <h2 class="section-title">SERVICES</h2>
  <article class="svc-card" style="left:112px">
    <div class="svc-photo" role="img" aria-label="Laptop with colourful charts and reports on a desk" style="background:linear-gradient(135deg,#e9eef3,#b9cde0 55%,#7fa3c8)"></div>
    <div class="svc-badge"><svg width="32" height="30" viewBox="0 0 32 30"><rect x="1" y="12" width="7" height="17" fill="#fff"/><path d="M10 28V13l7-11c3 0 4 2 3 5l-2 5h10c2 0 3 2 2 4l-4 10c-1 2-2 2-4 2z" fill="#fff"/></svg></div>
    <h3>DATA QUALITY</h3>
    <ul class="svc-list">
      <li><svg class="tick"><use href="#tick"/></svg>Global Address Verification</li>
      <li><svg class="tick"><use href="#tick"/></svg>Data Cleansing/Enrichment</li>
      <li><svg class="tick"><use href="#tick"/></svg>Match and Merge</li>
    </ul>
  </article>
  <article class="svc-card" style="left:625px">
    <div class="svc-photo" role="img" aria-label="Colleagues reviewing printed charts beside a laptop" style="background:linear-gradient(135deg,#d9d3c6,#a9a294 50%,#6a6d72)"></div>
    <div class="svc-badge"><svg width="26" height="30" viewBox="0 0 26 30"><ellipse cx="13" cy="5" rx="12" ry="4" fill="#fff"/><path d="M1 8c0 5 24 5 24 0v5c0 5-24 5-24 0zM1 16c0 5 24 5 24 0v5c0 5-24 5-24 0z" fill="#fff"/></svg></div>
    <h3>MASTER DATA MANAGEMENT</h3>
    <ul class="svc-list">
      <li><svg class="tick"><use href="#tick"/></svg>Integration</li>
      <li><svg class="tick"><use href="#tick"/></svg>Mastering</li>
      <li><svg class="tick"><use href="#tick"/></svg>Governance</li>
    </ul>
  </article>
</section>

<section class="connectors">
  <h2 class="section-title" style="top:2000px">RICH CONNECTORS</h2>
  <div class="box" style="left:112px;top:2103px;width:313px;height:318px">
    <svg class="icon" width="44" height="36" viewBox="0 0 44 36"><path d="M2 4h14l4 4h18v6H9L2 32z" fill="#f7b500"/><path d="M10 15h32l-8 18H2z" fill="#f7b500" opacity=".8"/></svg>
    <h3 style="top:78px">Applications</h3>
    <ul style="top:123px">
      <li><svg class="tick"><use href="#tick"/></svg>Trindavex</li>
      <li><svg class="tick"><use href="#tick"/></svg>FieldNexa</li>
      <li><svg class="tick"><use href="#tick"/></svg>Corvane</li>
      <li><svg class="tick"><use href="#tick"/></svg>Ostrell Business Hub</li>
    </ul>
    <p class="soon" style="top:245px">Mirelle Ledgerline*<br>Kestra*</p>
  </div>
  <div class="box" style="left:443px;top:2103px;width:313px;height:318px">
    <svg class="icon" width="34" height="40" viewBox="0 0 34 40"><ellipse cx="17" cy="6" rx="16" ry="5" fill="#f7b500"/><path d="M1 10c0 6 32 6 32 0v7c0 6-32 6-32 0zM1 21c0 6 32 6 32 0v7c0 6-32 6-32 0z" fill="#f7b500"/></svg>
    <h3 style="top:78px">Databases</h3>
    <ul style="top:123px">
      <li><svg class="tick"><use href="#tick"/></svg>Ostrell</li>
      <li><svg class="tick"><use href="#tick"/></svg>MyQuill</li>
      <li><svg class="tick"><use href="#tick"/></svg>Mirelle DataHouse</li>
      <li><svg class="tick"><use href="#tick"/></svg>Pelgrin SQL</li>
      <li><svg class="tick"><use href="#tick"/></svg>Idrun D2</li>
    </ul>
    <p class="soon" style="top:265px">Terravault*</p>
  </div>
  <div class="box" style="left:775px;top:2103px;width:313px;height:318px">
    <svg class="icon" width="38" height="40" viewBox="0 0 38 40"><path d="M12 2h14l8 8v20H12z" fill="none" stroke="#f7b500" stroke-width="3"/><path d="M4 10h8M4 10v28h20v-8" fill="none" stroke="#f7b500" stroke-width="3"/></svg>
    <h3 style="top:78px">Files</h3>
    <ul style="top:123px">
      <li><svg class="tick"><use href="#tick"/></svg>CSV</li>
      <li><svg class="tick"><use href="#tick"/></svg>Delimited</li>
      <li><svg class="tick"><use href="#tick"/></svg>Sheetwise</li>
    </ul>
    <p class="soon" style="top:265px;font-size:13px">* Coming Soon</p>
  </div>
</section>

<section class="support">
  <h2 class="section-title" style="top:85px">SUPPORT</h2>
  <div class="box" style="left:112px;top:190px;width:313px;height:225px">
    <svg class="icon" style="top:40px" width="38" height="38" viewBox="0 0 38 38"><circle cx="19" cy="19" r="11" fill="#f7b500"/><path d="M19 2v8M19 28v8M2 19h8M28 19h8M7 7l6 6M25 25l6 6M31 7l-6 6M13 25l-6 6" stroke="#f7b500" stroke-width="4"/></svg>
    <h3 style="top:95px">Batch</h3>
    <ul style="top:140px"><li><svg class="tick"><use href="#tick"/></svg>On your schedule</li></ul>
  </div>
  <div class="box" style="left:443px;top:190px;width:313px;height:225px">
    <svg class="icon" style="top:42px" width="42" height="30" viewBox="0 0 42 30"><rect x="1" y="3" width="28" height="24" rx="3" fill="#f7b500"/><path d="M30 12l11-7v20l-11-7z" fill="#f7b500"/></svg>
    <h3 style="top:95px">Streaming</h3>
    <ul style="top:140px"><li><svg class="tick"><use href="#tick"/></svg>Always in sync</li></ul>
  </div>
  <div class="box" style="left:775px;top:190px;width:313px;height:225px">
    <svg class="icon" style="top:40px" width="42" height="36" viewBox="0 0 42 36"><ellipse cx="17" cy="13" rx="15" ry="11" fill="none" stroke="#f7b500" stroke-width="3"/><path d="M8 22l-4 8 10-5" fill="#f7b500"/><path d="M33 12c5 2 8 6 7 10-1 3-3 5-6 6l3 6-9-5c-5 0-9-2-11-5" fill="none" stroke="#f7b500" stroke-width="3"/></svg>
    <h3 style="top:95px">Real Time/Interactive</h3>
    <ul style="top:140px">
      <li><svg class="tick"><use href="#tick"/></svg>Autocomplete Anything</li>
      <li><svg class="tick"><use href="#tick"/></svg>Smart Search</li>
    </ul>
  </div>
</section>

<section class="blog">
  <h2 class="section-title" style="top:3118px">BLOG</h2>
  <article class="post" style="left:112px">
    <div class="post-photo" role="img" aria-label="Team meeting in a bright office around a presentation screen" style="background:linear-gradient(135deg,#cfd9e4,#7d95ad 55%,#3f4f63)"></div>
    <h3>Finibus Bonoruet Ma</h3>
    <div class="meta"><span>&#9635; 18/06/2018</span><span>|</span><span>&#9679; Jane Marlo</span></div>
    <p>Nam libero tempore, cum soluta no bis est eligendi optio cumque nihil imp edit quo minus id quod maxi</p>
    <span class="read-more">READ MORE</span>
  </article>
  <article class="post" style="left:443px">
    <div class="post-photo" role="img" aria-label="Analyst working at multiple monitors showing dashboards" style="background:linear-gradient(135deg,#3d4a5c,#6f8198 50%,#26303c)"></div>
    <h3>Finibus Bonoruet Ma</h3>
    <div class="meta"><span>&#9635; 18/06/2018</span><span>|</span><span>&#9679; Jane Marlo</span></div>
    <p>Nam libero tempore, cum soluta no bis est eligendi optio cumque nihil imp edit quo minus id quod maxi</p>
    <span class="read-more">READ MORE</span>
  </article>
  <article class="post" style="left:775px">
    <div class="post-photo" role="img" aria-label="Hand with pen pointing at printed financial charts" style="background:linear-gradient(135deg,#e8e4dc,#b7c3cf 55%,#5c7088)"></div>
    <h3>Finibus Bonoruet Ma</h3>
    <div class="meta"><span>&#9635; 18/06/2018</span><span>|</span><span>&#9679; Jane Marlo</span></div>
    <p>Nam libero tempore, cum soluta no bis est eligendi optio cumque nihil imp edit quo minus id quod maxi</p>
    <span class="read-more">READ MORE</span>
  </article>
</section>

<footer class="contact">
  <h2 class="section-title">CONTACT US</h2>
  <h4 style="left:112px">CONTACT FORM</h4>
  <h4 style="left:795px">CONTACT INFORMATION</h4>
  <div class="field" style="left:112px;top:253px;width:310px">First Name</div>
  <div class="field" style="left:432px;top:253px;width:310px">Last Name</div>
  <div class="field" style="left:112px;top:297px;width:310px">Email</div>
  <div class="field" style="left:432px;top:297px;width:310px">Phone Number</div>
  <div class="field" style="left:112px;top:343px;width:630px;height:82px">Comments</div>
  <div class="submit">SUBMIT</div>

  <div class="info" style="top:245px">
    <span class="pin"><svg width="14" height="18" viewBox="0 0 14 18"><path d="M7 17S1 10 1 6.5a6 6 0 0112 0C13 10 7 17 7 17z" fill="#f7b500"/><circle cx="7" cy="6.5" r="2.2" fill="#2a2a2a"/></svg></span>
    <span>4810 Harlow Crest<br>Suite 310 Alder Vale, CA 94077</span>
  </div>
  <div class="info" style="top:313px">
    <span class="pin"><svg width="16" height="16" viewBox="0 0 16 16"><path d="M3 1l3 3-2 2c1 3 3 5 6 6l2-2 3 3-2 2C7 15 1 9 1 3z" fill="#f7b500"/></svg></span>
    <span>(555)013-4591</span>
  </div>
  <div class="info" style="top:372px">
    <span class="pin"><svg width="16" height="12" viewBox="0 0 16 12"><rect x="0.5" y="0.5" width="15" height="11" fill="#f7b500"/><path d="M1 1l7 6 7-6" fill="none" stroke="#2a2a2a" stroke-width="1.4"/></svg></span>
    <span>info@zolvarin.example</span>
  </div>
  <div class="socials"><span></span><span></span><span></span><span></span></div>

  <div class="footline"></div>
  <p class="copyright">Copyright © 2018, Zolvarin Data. All rights reserved.</p>
</footer>

</body>
</html>
```